Business Card Design

I need a business card for a new company based in Australia called "MedLinkora".

Its a cloud program for GPs that allows them to search for the specialist they require using a simple user friendly tool.

I would like the colours to match those in the program (the colours in the logo attached).

The final design should reflect the programs clarity, ease of use and professionalism.

Target Market(s)

GPs and other Health Professionals

Industry/Entity Type

Business

Contact Information for Business Card

MedLinkora; The Whole Consultant Index; Marla Voss CEO; 0438215967; marla@medlinkora.example; www.medlinkora.example

Requirements
Must have
• Must have the logo attached; the web address and my name and phone number
Nice to have
• the slogan "The Whole Consultant Index"

```html
<!DOCTYPE html>
<html lang="en">
<head>
<meta charset="utf-8">
<title>MedLinkora Business Card</title>
<link rel="stylesheet" href="https://fonts.googleapis.com/css2?family=Questrial&family=Open+Sans:wght@400;600;700&display=swap">
<style>
  :root {
    --brand-cyan: #00aee6;
    --ink-dark: #333333;
    --card-white: #ffffff;
    --rule-grey: #c8c8c8;
    --backdrop: #eceae6;
  }
  * { box-sizing: border-box; margin: 0; padding: 0; }
  html, body {
    width: 1200px; height: 829px; overflow: hidden;
    background: var(--backdrop);
  }
  .stage {
    width: 1200px; height: 829px;
    display: flex; align-items: center; justify-content: center; gap: 50px;
  }
  .card {
    position: relative;
    width: 530px; height: 303px;
    background: var(--card-white);
    box-shadow: 0 6px 18px rgba(0,0,0,0.12);
    overflow: hidden;
  }
  .brand {
    font-family: "Questrial", sans-serif;
    color: var(--brand-cyan);
    line-height: 1;
    letter-spacing: -1px;
    text-align: center;
    white-space: nowrap;
  }

  /* Front */
  .card--front .brand {
    position: absolute; left: 0; right: 0; top: 34px;
    font-size: 54px;
  }
  .card--front .person {
    position: absolute; left: 0; right: 0; top: 108px; text-align: center;
    font-family: "Open Sans", sans-serif; font-weight: 700;
    color: var(--brand-cyan); font-size: 20px; line-height: 1.2;
  }
  .card--front .person .role { font-weight: 400; font-size: 12px; }
  .card--front .rule {
    position: absolute; left: 0; right: 0; top: 150px; height: 2px;
    background: var(--rule-grey);
  }
  .card--front .contact-band {
    position: absolute; left: 0; right: 0; top: 156px; bottom: 0;
    background: var(--brand-cyan);
    color: var(--card-white);
    font-family: "Open Sans", sans-serif;
    display: flex; flex-direction: column; align-items: center; justify-content: center; gap: 18px;
  }
  .contact-line { display: flex; align-items: center; gap: 8px; white-space: nowrap; }
  .contact-line--phone { font-size: 22px; font-weight: 600; }
  .contact-line--net { font-size: 14px; gap: 18px; }
  .contact-item { display: flex; align-items: center; gap: 6px; }
  .icon { flex: none; }

  /* Back */
  .card--back .brand {
    position: absolute; left: 0; right: 0; top: 100px;
    font-size: 60px;
  }
  .card--back .web {
    position: absolute; left: 0; right: 0; top: 186px; text-align: center;
    font-family: "Open Sans", sans-serif; font-size: 18px; font-weight: 600;
    letter-spacing: 1px; color: var(--ink-dark);
  }
</style>
</head>
<body>
<main class="stage">

  <section class="card card--front" aria-label="Business card front">
    <div class="brand">MedLinkora</div>
    <div class="person">Marla Voss, <span class="role">CEO</span></div>
    <div class="rule"></div>
    <div class="contact-band">
      <div class="contact-line contact-line--phone">
        <svg class="icon" width="20" height="20" viewBox="0 0 20 20" aria-hidden="true">
          <circle cx="10" cy="10" r="9" fill="#fff"/>
          <path d="M7 5.5c.6-.3 1.1 0 1.3.5l.6 1.6c.2.5 0 .9-.4 1.2l-.5.4c.5 1.2 1.3 2 2.5 2.6l.4-.5c.3-.4.8-.5 1.2-.3l1.6.7c.5.2.7.8.4 1.3-.6 1-1.6 1.4-2.7 1-2.4-.9-4.1-2.6-5-5-.4-1.1 0-2.2 1-2.9z" fill="var(--brand-cyan)"/>
        </svg>
        <span>0438215967</span>
      </div>
      <div class="contact-line contact-line--net">
        <span class="contact-item">
          <svg class="icon" width="16" height="16" viewBox="0 0 16 16" aria-hidden="true">
            <circle cx="8" cy="8" r="7.5" fill="#fff"/>
            <rect x="3.5" y="5" width="9" height="6.5" fill="none" stroke="var(--brand-cyan)" stroke-width="1.2"/>
            <path d="M3.5 5 8 9l4.5-4" fill="none" stroke="var(--brand-cyan)" stroke-width="1.2"/>
          </svg>
          marla@medlinkora.example
        </span>
        <span class="contact-item">
          <svg class="icon" width="16" height="16" viewBox="0 0 16 16" aria-hidden="true">
            <circle cx="8" cy="8" r="7.5" fill="#fff"/>
            <circle cx="8" cy="8" r="5" fill="none" stroke="var(--brand-cyan)" stroke-width="1.1"/>
            <ellipse cx="8" cy="8" rx="2.2" ry="5" fill="none" stroke="var(--brand-cyan)" stroke-width="1"/>
            <path d="M3 8h10" stroke="var(--brand-cyan)" stroke-width="1"/>
          </svg>
          www.medlinkora.example
        </span>
      </div>
    </div>
  </section>

  <section class="card card--back" aria-label="Business card back">
    <div class="brand">MedLinkora</div>
    <div class="web">www.medlinkora.example</div>
  </section>

</main>
</body>
</html>
```